Fitness Equipment Repair Business Needs a Catchy New Business Card

We have an existing business card, however, it is quite plain and boring. We are expanding primarily in the commercial area (gyms, studios, apartment complexes etc). The business card will serve as eye candy to those managers/owners that can't be met for a face to face.
Originally I was planning for a brochure as well, but all of our information is better summarized on our website. (brightloopservice.ca).
I would like the card to match the colour scheme of the website and utilize the logo. It should have a professional clean feel to it, however, a little colouring outside the lines wouldn't hurt.
The example card is for my service technician (Colin Marsh). If possible I would like to be able to edit the text to use for more than one person.

Industry/Entity Type

Appliance Repair

Contact Information for Business Card

Clean, crisp and professional but needs to be eye catching. Preferably using the black, white and red colour scheme matching the website. Double sided would be nice, but is not necessary.

Colors
ec1f27
ffffff
000000

Requirements
Must have
• Must be able to edit name, phone number and title to use for multiple people. Must show the company website (brightloopservice.ca).

```html
<!DOCTYPE html>
<html lang="en">
<head>
<meta charset="utf-8">
<title>Bright Loop Service – Business Card</title>
<link rel="stylesheet" href="https://fonts.googleapis.com/css2?family=Cinzel:wght@500&family=PT+Sans:wght@400;700&family=Tinos&display=swap">
<style>
  :root {
    --red: #ec1f27;
    --black: #000000;
    --white: #ffffff;
    --backdrop: #ece9e4;
    --rule: rgba(255,255,255,0.55);
  }
  html, body {
    margin: 0;
    width: 1200px;
    height: 900px;
    overflow: hidden;
    background: var(--backdrop);
  }
  .canvas { position: relative; width: 1200px; height: 900px; }

  .card {
    position: absolute;
    width: 520px;
    height: 297px;
    overflow: hidden;
    box-shadow: 0 6px 18px rgba(0,0,0,0.18);
  }
  .card--front { left: 90px; top: 130px; }
  .card--back  { left: 590px; top: 470px; }

  .band { position: absolute; left: 0; width: 100%; }
  .band--red { background: var(--red); }
  .band--black { background: var(--black); }

  .brand-title {
    position: absolute;
    margin: 0;
    font-family: "Cinzel", serif;
    font-weight: 500;
    font-size: 25px;
    line-height: 30px;
    letter-spacing: 1px;
    color: var(--white);
    white-space: nowrap;
  }

  .logo-mark {
    position: absolute;
    display: flex;
    align-items: center;
    gap: 7px;
  }
  .logo-mark__dot {
    width: 16px; height: 16px;
    border-radius: 50%;
    background: var(--white);
  }
  .logo-mark__name {
    font-family: "PT Sans", sans-serif;
    font-weight: 700;
    font-size: 22px;
    line-height: 26px;
    color: var(--white);
  }

  /* front */
  .card--front .band--red { top: 0; height: 205px; }
  .card--front .band--black { top: 205px; height: 92px; }
  .card--front .logo-mark { left: 38px; top: 114px; }
  .card--front .brand-title { left: 140px; top: 112px; }
  .front-web {
    position: absolute;
    right: 92px; top: 236px;
    font-family: "Tinos", serif;
    font-size: 17px;
    color: var(--white);
  }

  /* back */
  .card--back .band--black.top { top: 0; height: 120px; }
  .card--back .band--red { top: 120px; height: 108px; }
  .card--back .band--black.bottom { top: 228px; height: 69px; }
  .card--back .logo-mark { left: 52px; top: 58px; }
  .card--back .brand-title { left: 168px; top: 56px; }

  .person {
    position: absolute;
    right: 230px; top: 128px;
    text-align: right;
    font-family: "PT Sans", sans-serif;
    color: var(--white);
    line-height: 1.2;
  }
  .person__name { font-size: 17px; font-weight: 700; margin: 0; }
  .person__title { font-size: 13px; margin: 0 0 3px; }
  .person__address { font-size: 14px; margin: 0; font-style: normal; }

  .divider {
    position: absolute;
    left: 302px; top: 130px;
    width: 1px; height: 86px;
    background: var(--rule);
  }
  .contacts {
    position: absolute;
    left: 314px; top: 134px;
    margin: 0; padding: 0;
    list-style: none;
    font-family: "PT Sans", sans-serif;
    font-size: 12px;
    color: var(--white);
  }
  .contacts li { display: flex; align-items: center; gap: 6px; height: 19px; }
  .contacts svg { width: 10px; height: 10px; fill: var(--white); flex: none; }

  .tagline {
    position: absolute;
    left: 0; right: 0; top: 250px;
    margin: 0;
    text-align: center;
    font-family: "Tinos", serif;
    font-size: 17px;
    color: var(--white);
  }
</style>
</head>
<body>
<div class="canvas">

  <section class="card card--front" aria-label="Card front">
    <div class="band band--red"></div>
    <div class="band band--black"></div>
    <div class="logo-mark"><span class="logo-mark__dot"></span><span class="logo-mark__name">BLS</span></div>
    <h1 class="brand-title">Bright Loop Service</h1>
    <span class="front-web">www.brightloopservice.ca</span>
  </section>

  <section class="card card--back" aria-label="Card back">
    <div class="band band--black top"></div>
    <div class="band band--red"></div>
    <div class="band band--black bottom"></div>
    <div class="logo-mark"><span class="logo-mark__dot"></span><span class="logo-mark__name">BLS</span></div>
    <h2 class="brand-title">Bright Loop Service</h2>

    <div class="person">
      <p class="person__name">Colin Marsh</p>
      <p class="person__title">Managing Director</p>
      <address class="person__address">1234, Address GoesHere,<br>Country, 12345</address>
    </div>

    <div class="divider"></div>
    <ul class="contacts">
      <li><svg viewBox="0 0 10 10"><path d="M1 2.5C1 1.5 2 1 5 1s4 .5 4 1.5V4H7V3H3v1H1zM2 5h6l1 4H1z"/></svg>(044) 555014207</li>
      <li><svg viewBox="0 0 10 10"><path d="M3 0h4a1 1 0 0 1 1 1v8a1 1 0 0 1-1 1H3a1 1 0 0 1-1-1V1a1 1 0 0 1 1-1zm0 1.5v6h4v-6z"/></svg>(044)555014207</li>
      <li><svg viewBox="0 0 10 10"><path d="M0 2h10v6H0zM.8 2.6 5 5.6l4.2-3z" fill-rule="evenodd"/></svg>info@brightloopservice.ca</li>
      <li><svg viewBox="0 0 10 10"><circle cx="5" cy="5" r="4.5"/></svg>www.brightloopservice.ca</li>
    </ul>

    <p class="tagline">When your equipment can't finish their workout, give us a call!</p>
  </section>

</div>
</body>
</html>
```